Accounting firm needing business card / letterhead designed
Marcus L. Trenholm, CPA
marcus@veltrowledger.com
www.veltrowledger.com
842 E Alder Ave Corvale, MN 43827
555-562-0974

```html
<!DOCTYPE html>
<html lang="en">
<head>
<meta charset="utf-8">
<title>Veltrow Ledger — Business Card</title>
<link rel="stylesheet" href="https://fonts.googleapis.com/css2?family=Barlow+Semi+Condensed:wght@500;600;700&display=swap">
<style>
  :root {
    --backdrop: #e6e6e6;
    --navy: #22134d;
    --green: #5cb82e;
    --card-white: #f7f7f7;
    --ink: #1d1d24;
  }
  * { margin: 0; padding: 0; box-sizing: border-box; }
  html, body {
    width: 1200px;
    height: 576px;
    overflow: hidden;
    background: var(--backdrop);
    font-family: "Barlow Semi Condensed", "Arial Narrow", sans-serif;
  }
  .canvas {
    position: relative;
    width: 1200px;
    height: 576px;
  }
  .card {
    position: absolute;
    border-radius: 14px;
    box-shadow: 0 3px 6px rgba(0,0,0,0.18);
  }
  .card--front {
    left: 82px; top: 139px;
    width: 484px; height: 293px;
    background: var(--navy);
  }
  .card--back {
    left: 602px; top: 138px;
    width: 480px; height: 291px;
    background: var(--card-white);
  }
  .brand-name {
    position: absolute;
    font-weight: 700;
    text-transform: uppercase;
    letter-spacing: 0.04em;
    line-height: 1;
    white-space: nowrap;
  }
  .card--front .brand-name {
    left: 50%; top: 50%;
    transform: translate(-50%, -50%);
    color: #ffffff;
    font-size: 38px;
  }
  .card--back .brand-name {
    left: 32px; top: 145px;
    transform: translateY(-50%);
    color: var(--navy);
    font-size: 25px;
  }
  .contact {
    position: absolute;
    left: 264px; top: 90px;
    color: var(--ink);
  }
  .contact__name {
    font-weight: 700;
    font-size: 17px;
    line-height: 20px;
    color: var(--navy);
    margin-bottom: 14px;
    white-space: nowrap;
  }
  .contact__title { color: var(--green); }
  .contact__list { list-style: none; }
  .contact__item {
    display: flex;
    align-items: center;
    font-size: 12.5px;
    font-weight: 500;
    height: 18px;
    white-space: nowrap;
  }
  .contact__icon {
    width: 10px; height: 10px;
    margin: 0 14px 0 4px;
    flex: none;
  }
  .contact__address {
    font-size: 12.8px;
    font-weight: 500;
    margin-top: 2px;
    white-space: nowrap;
  }
</style>
</head>
<body>
<main class="canvas">
  <section class="card card--front" aria-label="Card front">
    <span class="brand-name">Veltrow Ledger</span>
  </section>

  <section class="card card--back" aria-label="Card back">
    <span class="brand-name">Veltrow Ledger</span>

    <div class="contact">
      <p class="contact__name">Marcus L. Trenholm, <span class="contact__title">CPA</span></p>
      <ul class="contact__list">
        <li class="contact__item">
          <svg class="contact__icon" viewBox="0 0 10 10" aria-hidden="true">
            <path d="M1 3.2 Q5 0.8 9 3.2 L8 4.4 L6.6 3.8 L6.6 3 Q5 2.5 3.4 3 L3.4 3.8 L2 4.4 Z" fill="var(--green)"/>
            <rect x="2.4" y="5" width="5.2" height="4" rx="0.8" fill="var(--green)"/>
          </svg>
          555-562-0974
        </li>
        <li class="contact__item">
          <svg class="contact__icon" viewBox="0 0 10 10" aria-hidden="true">
            <rect x="0.5" y="2" width="9" height="6.4" fill="var(--green)"/>
            <path d="M0.8 2.3 L5 5.6 L9.2 2.3" fill="none" stroke="#ffffff" stroke-width="0.9"/>
          </svg>
          marcus@veltrowledger.com
        </li>
        <li class="contact__item">
          <svg class="contact__icon" viewBox="0 0 10 10" aria-hidden="true">
            <circle cx="5" cy="5" r="4.5" fill="var(--green)"/>
            <path d="M0.6 5 H9.4 M5 0.6 Q2.4 5 5 9.4 M5 0.6 Q7.6 5 5 9.4" fill="none" stroke="#ffffff" stroke-width="0.7"/>
          </svg>
          www.veltrowledger.com
        </li>
      </ul>
      <p class="contact__address">842 E Alder Ave Corvale, MN 43827</p>
    </div>
  </section>
</main>
</body>
</html>
```